We are a recruitment company based in Norwich/Cambridge England.
I have included our company logo which we want to remain the same.

What we are looking for is a new creative Business card which will really stand out!!

Contact Information for Business Card

Harriet Dunmore
email: Harriet@plavex.co.uk
Address: Brackwell House
Fenmoor Enterprise Park
Partridge Way
Norwich
QB9 3KX
Tel:01632 960418

```html
<!DOCTYPE html>
<html lang="en">
<head>
<meta charset="utf-8">
<title>Plavex Business Card</title>
<link rel="stylesheet" href="https://fonts.googleapis.com/css2?family=Quicksand:wght@400;500;700&display=swap">
<style>
  :root {
    --backdrop: #2e2e30;
    --grey: #958b91;
    --grey-dark: #5d585b;
    --green: #a2d20f;
    --green-soft: #9cc62a;
    --white: #ffffff;
  }
  * { margin: 0; padding: 0; box-sizing: border-box; }
  html, body { width: 1200px; height: 900px; overflow: hidden; }
  body {
    background: var(--backdrop);
    font-family: "Quicksand", sans-serif;
    position: relative;
  }
  .card {
    position: absolute;
    width: 700px;
    height: 400px;
    border-radius: 22px;
    overflow: hidden;
  }
  .card-front { left: 60px; top: 50px; background: var(--grey); }
  .card-back {
    left: 440px; top: 450px;
    background: linear-gradient(150deg, var(--green) 0%, var(--green-soft) 35%, #a09a9c 80%, var(--grey) 100%);
  }
  .front-shapes { position: absolute; inset: 0; }
  .brand {
    position: absolute;
    display: flex;
    align-items: center;
    font-weight: 700;
    line-height: 1;
  }
  .brand-dot { border-radius: 50%; background: var(--white); }
  .card-front .brand { left: 430px; top: 48px; gap: 12px; font-size: 42px; color: var(--green); }
  .card-front .brand-dot { width: 36px; height: 36px; }
  .card-back .brand { left: 190px; top: 155px; gap: 18px; font-size: 64px; color: var(--white); }
  .card-back .brand-dot { width: 70px; height: 70px; }
  .holder { position: absolute; left: 150px; top: 168px; color: var(--grey-dark); }
  .holder-name { font-size: 25px; font-weight: 700; letter-spacing: 0.5px; }
  .holder-role { font-size: 19px; font-weight: 500; margin-top: 2px; }
  .contact-list { list-style: none; margin-top: 16px; }
  .contact-list li {
    display: flex; align-items: center; gap: 9px;
    font-size: 17px; font-weight: 500; line-height: 28px;
  }
  .contact-list svg { width: 14px; height: 14px; flex: none; }
  .address {
    position: absolute; left: 470px; top: 205px;
    color: var(--white); font-size: 17px; font-weight: 500; line-height: 27px;
    font-style: normal;
  }
</style>
</head>
<body>
  <section class="card card-front">
    <svg class="front-shapes" viewBox="0 0 700 400" aria-hidden="true">
      <rect x="0" y="180" width="260" height="220" fill="var(--white)"/>
      <circle cx="250" cy="250" r="200" fill="var(--green)"/>
      <circle cx="250" cy="250" r="150" fill="var(--white)"/>
    </svg>
    <div class="brand"><span class="brand-dot"></span><span>Plavex</span></div>
    <div class="holder">
      <h1 class="holder-name">HARRIET DUNMORE</h1>
      <p class="holder-role">President</p>
      <ul class="contact-list">
        <li>
          <svg viewBox="0 0 16 16"><path fill="currentColor" d="M3.6 1.2l2.3 2.4-1.3 2a9 9 0 0 0 5.8 5.8l2-1.3 2.4 2.3-1.5 2.2C7.6 14.4 1.6 8.4 1.4 2.7z"/></svg>
          01632 960418
        </li>
        <li>
          <svg viewBox="0 0 16 16"><path fill="currentColor" d="M1 3h14v10H1zM2.5 4.5v.4L8 8.7l5.5-3.8v-.4z"/></svg>
          Harriet@plavex.co.uk
        </li>
        <li>
          <svg viewBox="0 0 16 16"><circle cx="8" cy="8" r="6.5" fill="none" stroke="currentColor" stroke-width="1.5"/><path fill="none" stroke="currentColor" stroke-width="1.2" d="M1.5 8h13M8 1.5c-3 3.5-3 9.5 0 13M8 1.5c3 3.5 3 9.5 0 13"/></svg>
          www.plavex.co.uk
        </li>
      </ul>
    </div>
    <address class="address">
      Brackwell House<br>
      Fenmoor Enterprise Park<br>
      Partridge Way Norwich QB9 3KX
    </address>
  </section>

  <section class="card card-back">
    <div class="brand"><span class="brand-dot"></span><span>Plavex</span></div>
  </section>
</body>
</html>
```